Calvanto Group Real Estate Company business cards

New business card design, we are generally happy with the basic layout of the existing front of business card, (feel free to change) but require a head shot photo on the back side.

http://www.calvanto.com.au/

Attached logos, and existing business card

------------------------------

Target Market(s)

Real estate

Industry/Entity Type

Real Estate

Contact Information for Business Card

Standard size double sided

Font styles to use
Other font styles liked:
• Futura

Requirements
Must have
• Photo head shot on the back side
Nice to have
• yes
Should not have
• No

```html
<!DOCTYPE html>
<html lang="en">
<head>
<meta charset="utf-8">
<title>Calvanto Group – Business Cards</title>
<link rel="stylesheet" href="https://fonts.googleapis.com/css2?family=Open+Sans:wght@400;600;700&display=swap">
<style>
  :root {
    --navy: #2e2463;
    --orange: #f7941d;
    --white: #ffffff;
    --black: #0d0d0d;
    --ink: #2b2b2b;
    --backdrop: #e9e6e1;
  }
  * { box-sizing: border-box; margin: 0; padding: 0; }
  html, body {
    width: 1200px; height: 900px; overflow: hidden;
    background: var(--backdrop);
    font-family: "Open Sans", Arial, sans-serif;
  }
  .card {
    position: absolute; left: 250px;
    width: 700px; height: 400px; overflow: hidden;
    box-shadow: 0 6px 18px rgba(0,0,0,.18);
  }
  /* Back side */
  .card--back {
    top: 40px;
    background: linear-gradient(100deg, #000 0%, #1a1a1a 45%, #000 70%);
    color: var(--white);
  }
  .back-brand { position: absolute; left: 40px; top: 38px; width: 330px; text-align: center; }
  .back-brand .brand-name { font-size: 64px; font-weight: 600; letter-spacing: 1px; line-height: 1; color: var(--white); }
  .services { margin-top: 16px; font-size: 17px; letter-spacing: 1px; }
  .tagline {
    position: absolute; left: 40px; top: 190px;
    font-size: 21px; font-weight: 700; letter-spacing: .5px;
  }
  .headshot {
    position: absolute; right: 0; top: 0; width: 310px; height: 400px;
    background: linear-gradient(180deg, #2a2a2a 0%, #3a3f57 45%, #27314f 100%);
  }
  /* Front side */
  .card--front { top: 460px; background: var(--white); color: var(--navy); }
  .card-graphics { position: absolute; inset: 0; }
  .person { position: absolute; left: 74px; top: 22px; }
  .person .name { font-size: 22px; font-weight: 700; line-height: 1.1; }
  .person .role { font-size: 13px; color: var(--ink); }
  .contact { position: absolute; left: 60px; top: 100px; font-size: 16px; color: var(--ink); line-height: 1.4; }
  .contact .company { font-size: 17px; font-weight: 700; color: var(--navy); }
  .contact .abn { margin-bottom: 8px; }
  .contact .abn b { color: var(--navy); }
  .contact li { list-style: none; display: flex; align-items: center; gap: 12px; line-height: 1.5; }
  .contact svg { width: 13px; height: 13px; fill: var(--navy); flex: none; }
  .front-brand {
    position: absolute; left: 380px; top: 120px;
    font-size: 72px; font-weight: 600; line-height: 1; color: var(--navy);
    letter-spacing: 1px;
  }
</style>
</head>
<body>

<section class="card card--back">
  <div class="back-brand">
    <div class="brand-name">calvanto</div>
    <div class="services">Buy &nbsp;|&nbsp; Sell &nbsp;|&nbsp; Rent</div>
  </div>
  <div class="tagline">LET US SHOW YOU PROPERTY</div>
  <div class="headshot" role="img" aria-label="Head shot photo of the agent in a navy suit"></div>
</section>

<section class="card card--front">
  <svg class="card-graphics" viewBox="0 0 700 400" width="700" height="400" aria-hidden="true">
    <polygon points="14,20 40,20 14,44" fill="var(--orange)"/>
    <polygon points="44,20 66,20 66,62 14,62" fill="var(--navy)"/>
    <polygon points="0,256 300,256 280,280 0,280" fill="var(--orange)"/>
    <polygon points="318,318 700,318 700,372 296,372" fill="var(--navy)"/>
  </svg>

  <div class="person">
    <div class="name">Daniel Tran</div>
    <div class="role">Director</div>
  </div>

  <div class="contact">
    <div class="company">Calvanto Group</div>
    <div class="abn"><b>ABN:</b> 12 345 678 901</div>
    <ul>
      <li><svg viewBox="0 0 16 16"><path d="M3.5 1l2.5 3-1.5 2a9 9 0 0 0 5.5 5.5l2-1.5 3 2.5-1.5 2.5C7 15 1 9 1 2.5z"/></svg>0400 555 218</li>
      <li><svg viewBox="0 0 16 16"><path d="M1 3h14v10H1z M1 3l7 6 7-6" stroke="var(--white)" stroke-width="1.2"/></svg>daniel.tran@calvanto.com.au</li>
      <li><svg viewBox="0 0 16 16"><circle cx="8" cy="8" r="7"/></svg>www.calvanto.com.au</li>
    </ul>
  </div>

  <div class="front-brand">calvanto</div>
</section>

</body>
</html>
```